RWT Fittings Ltd Business Cards

We need a business card with our business logo. We provide window and door installations on high-rises in west coast British Colombia, Canada.

I would like my business information and details on one side of the card, and the other side the company name with logo

Target Market(s)

General Contractors

Industry/Entity Type

Construction

Contact Information for Business Card

one side i want my company name and logo in the dark theme logo that i provided

Requirements
Must have
• Marco Peltieri, 16045518293, RWTFittings@mailbox-demo.com, 1407-5194 Linden Row Burnaby BC, V5H 2K9, Owner & Manager

```html
<!DOCTYPE html>
<html lang="en">
<head>
<meta charset="utf-8">
<title>RWT Fittings Ltd – Business Card</title>
<link href="https://fonts.googleapis.com/css2?family=Open+Sans:wght@400;600;700&display=swap" rel="stylesheet">
<style>
  :root {
    --page-bg: #dcd7cf;
    --card-light: #ece8e1;
    --card-dark: #1f1d1c;
    --teal: #2696b5;
    --teal-bright: #2fb3cf;
    --mark-grey: #6e6e6e;
    --text-light: #d9d3c8;
    --text-muted: #c7c0b4;
  }
  * { margin: 0; padding: 0; box-sizing: border-box; }
  html, body {
    width: 1200px;
    height: 1047px;
    overflow: hidden;
    background: var(--page-bg);
    font-family: "Open Sans", Arial, sans-serif;
  }
  .card {
    position: absolute;
    left: 100px;
    top: 251px;
    width: 1000px;
    height: 545px;
    border-radius: 20px;
    overflow: hidden;
    box-shadow: 0 10px 30px rgba(0,0,0,0.18);
  }
  .card-shapes { position: absolute; inset: 0; }
  .brand {
    position: absolute;
    top: 78px;
    left: 0;
    width: 100%;
    display: flex;
    justify-content: center;
    align-items: center;
    gap: 26px;
  }
  .brand-square {
    width: 104px;
    height: 104px;
    background: var(--mark-grey);
  }
  .brand-name {
    font-weight: 700;
    font-size: 66px;
    letter-spacing: 1px;
    color: var(--teal);
    line-height: 1;
  }
  .holder {
    position: absolute;
    right: 558px;
    top: 358px;
    text-align: right;
  }
  .holder-name {
    font-weight: 700;
    font-size: 31px;
    color: var(--teal);
    letter-spacing: 0.5px;
    line-height: 1.1;
  }
  .holder-title {
    font-size: 22px;
    color: var(--text-muted);
    margin-top: 6px;
  }
  .divider {
    position: absolute;
    left: 485px;
    top: 350px;
    width: 2px;
    height: 96px;
    background: var(--teal);
  }
  .contacts {
    position: absolute;
    left: 512px;
    top: 346px;
    list-style: none;
  }
  .contacts li {
    display: flex;
    align-items: center;
    gap: 10px;
    font-size: 21px;
    color: var(--text-light);
    height: 33px;
  }
  .contacts svg { width: 20px; height: 20px; flex: none; }
  .address {
    position: absolute;
    left: 0;
    top: 474px;
    width: 100%;
    height: 33px;
    line-height: 33px;
    text-align: center;
    font-size: 21px;
    color: var(--text-light);
  }
</style>
</head>
<body>
  <div class="card">
    <svg class="card-shapes" width="1000" height="545" viewBox="0 0 1000 545">
      <rect width="1000" height="545" fill="var(--card-light)"/>
      <path d="M0 222 Q500 375 1000 222 L1000 545 L0 545 Z" fill="var(--card-dark)"/>
      <path d="M60 204 Q500 352 950 200" fill="none" stroke="var(--teal)" stroke-width="4"/>
      <rect x="0" y="474" width="1000" height="33" fill="var(--teal-bright)" opacity="0.85"/>
    </svg>

    <div class="brand">
      <div class="brand-square"></div>
      <div class="brand-name">RWT Fittings Ltd</div>
    </div>

    <div class="holder">
      <div class="holder-name">MARCO PELTIERI</div>
      <div class="holder-title">Owner &amp; Manager</div>
    </div>

    <div class="divider"></div>

    <ul class="contacts">
      <li>
        <svg viewBox="0 0 24 24"><path fill="var(--teal)" d="M6.6 10.8a15 15 0 0 0 6.6 6.6l2.2-2.2c.3-.3.7-.4 1-.2 1.1.4 2.300.6 3.6.6.6 0 1 .4 1 1V20c0 .6-.4 1-1 1A17 17 0 0 1 3 4c0-.6.4-1 1-1h3.5c.6 0 1 .4 1 1 0 1.3.2 2.5.6 3.6.1.3 0 .7-.2 1z"/></svg>
        16045518293
      </li>
      <li>
        <svg viewBox="0 0 24 24"><rect x="2" y="5" width="20" height="14" rx="2" fill="var(--teal)"/><path d="M3 6l9 7 9-7" fill="none" stroke="var(--card-dark)" stroke-width="1.8"/></svg>
        RWTFittings@mailbox-demo.com
      </li>
      <li>
        <svg viewBox="0 0 24 24"><circle cx="12" cy="12" r="10" fill="var(--teal)"/><path d="M2 12h20M12 2c3 3 3 17 0 20M12 2c-3 3-3 17 0 20" fill="none" stroke="var(--card-dark)" stroke-width="1.4"/></svg>
        www.rwtfittings-demo.com
      </li>
    </ul>

    <div class="address">1407-5194 Linden Row Burnaby BC, V5H 2K9</div>
  </div>
</body>
</html>
```